New Physiotherapy Practice Website for an Award winning, Experienced Physio

Wanting to relaunch a 1 person physio practice. This is my academic CV
https://staffpages.wexmoor.edu.au/en/people/darren-koval.
I want a simple, clear website that emphases My Name, My Experience, My Expertise, Location with a map, and Phone number (+ link to an online booking platform)
There aren't many clinicians around who also research and teach. I am unique with the awards I have won in each domain. I care about my patients, I listen, I am evidence based in my approach, I work WITH my clients I don't work AT my clients. I have experience with very acute through to chronic conditions, I have a range of expertise that set me apart in terms of advanced practice, hands- on technique and exercise based interventions. I am happy treating all musculoskeletal conditions but have a particular expertise in lower limb diagnosis and rehab and in providing second opinions. We have a large gym, medical, imaging, pharmacy in the same building. Easy parking and free for patients. Early morning bookings (0800) available but limited.
Facility is at https://www.wexmoor.edu.au/health-clinics/contact-us
Target Market(s)
Local community needing injury diagnosis and treatment. Looking for skilled and experienced physio. "Hands of Experience"
Industry/Entity Type
Health (Physiotherapy)
Coding
Coded - Design and coding required
Number of Pages Required
1 page
Requirements
Must have
- Online booking button and phone number
Should not have
- Not too much focus on my research

```html
<!DOCTYPE html>
<html lang="en">
<head>
<meta charset="utf-8">
<title>Dr Darren Koval — Physiotherapy</title>
<link rel="stylesheet" href="https://fonts.googleapis.com/css2?family=Montserrat:wght@600;700;800&family=Nunito:wght@400;600&display=swap">
<style>
:root{
  --blue:#0b5e9c;
  --blue-deep:#0a4f86;
  --green:#5aab86;
  --green-light:#7cc3a0;
  --green-footer:#55a984;
  --green-dark:#1f5f4c;
  --portrait-top:#8aa6d8;
  --portrait-bottom:#5f7fc0;
  --ink:#1d1d1f;
  --text:#3a3a3a;
  --white:#ffffff;
  --bg-soft:#f6f6f7;
}
*{margin:0;padding:0;box-sizing:border-box}
html,body{width:1200px;height:2161px;overflow:hidden;background:var(--white)}
body{font-family:"Nunito",sans-serif;color:var(--text);position:relative}
.site-header{height:65px;display:flex;align-items:center;justify-content:space-between;padding:0 132px 0 130px}
.brand{font-family:"Montserrat",sans-serif;font-weight:800;font-size:22px;color:var(--blue);letter-spacing:.3px}
.nav{display:flex;gap:30px;font-family:"Montserrat",sans-serif;font-weight:600;font-size:12.5px;letter-spacing:.5px;color:var(--ink)}
.nav .active{color:var(--green)}
.hero{position:absolute;top:65px;left:0;width:1200px;height:446px;background:radial-gradient(circle at 70% 40%,#0f6aaa 0%,var(--blue) 45%,var(--blue-deep) 100%);overflow:hidden}
.hero-ring{position:absolute;left:0;top:0}
.hero-portrait{position:absolute;left:640px;top:18px;width:320px;height:428px;border-radius:160px 160px 0 0;background:linear-gradient(180deg,var(--portrait-top),var(--portrait-bottom))}
.hero-title{position:absolute;left:129px;top:98px;font-family:"Montserrat",sans-serif;font-weight:800;font-size:40px;color:var(--white);letter-spacing:.5px}
.phone-box{position:absolute;left:131px;top:165px;width:300px;height:64px;border:2px solid var(--green);border-radius:8px;display:flex;align-items:center;gap:12px;padding-left:18px;color:var(--white);font-family:"Montserrat",sans-serif;font-weight:700;font-size:27px}
.book-btn{position:absolute;left:135px;top:256px;width:190px;height:59px;background:var(--green);border-radius:6px;color:var(--white);font-family:"Montserrat",sans-serif;font-weight:700;font-size:18px;display:flex;align-items:center;justify-content:center;box-shadow:0 6px 14px rgba(0,0,0,.25)}
.features{position:absolute;top:511px;left:0;width:1200px;height:69px;background:var(--green);display:flex}
.feature{display:flex;align-items:center;justify-content:center;gap:12px;color:var(--white);font-family:"Montserrat",sans-serif;font-weight:700;font-size:16.5px;border-right:1px solid rgba(255,255,255,.35)}
.feature:last-child{border-right:none}
.experience{position:absolute;top:580px;left:0;width:1200px;height:636px}
.section-title{font-family:"Montserrat",sans-serif;font-weight:800;font-size:20px;color:var(--blue)}
.exp-title{position:absolute;left:130px;top:38px;display:flex;align-items:center;gap:22px}
.exp-title::after{content:"";width:188px;height:2px;background:var(--blue)}
.photo{position:absolute}
.photo-gym{left:131px;top:83px;width:380px;height:155px;background:linear-gradient(180deg,#d9d6cc,#8d8f92 55%,#3a3d45)}
.photo-clinic{left:131px;top:251px;width:380px;height:334px;background:linear-gradient(135deg,#3b3a38,#1c1d1f 60%,#55616c)}
.exp-text{position:absolute;left:548px;top:76px;width:520px;font-size:13.4px;line-height:18.45px;text-align:justify;color:var(--text)}
.exp-text p+p{margin-top:16px;text-align:left}
.services{position:absolute;top:1216px;left:0;width:1200px;height:408px;background:var(--bg-soft)}
.services .section-title{position:absolute;top:30px;width:100%;text-align:center}
.services-rule{position:absolute;left:582px;top:65px;width:36px;height:2px;background:var(--blue)}
.service{position:absolute;top:92px;width:297px}
.service .pic{height:245px}
.service h3{font-family:"Montserrat",sans-serif;font-weight:600;font-size:14.5px;letter-spacing:.7px;color:var(--ink);text-align:center;margin-top:17px}
.pic-msk{background:linear-gradient(135deg,#0b3450,#1d8fb0 55%,#e7743c)}
.pic-limb{background:radial-gradient(circle at 58% 65%,#e0473a 0%,#7b3a34 25%,#1b1b1d 70%)}
.pic-rehab{background:linear-gradient(160deg,#d5dde3,#2b6fb3 45%,#232a3c)}
.map{position:absolute;top:1624px;left:0;width:1200px;height:381px;background:linear-gradient(135deg,#eceef0,#e3e6e8 60%,#cfe3d3)}
.site-footer{position:absolute;top:2005px;left:0;width:1200px;height:156px;background:var(--green-footer);color:var(--white)}
.footer-top{display:flex;justify-content:space-between;align-items:center;padding:0 132px 0 128px;height:90px}
.footer-top .brand{color:var(--white)}
.footer-top .nav{color:var(--white)}
.footer-rule{margin:0 132px 0 130px;height:1px;background:rgba(255,255,255,.35)}
.copyright{text-align:center;font-size:12.5px;margin-top:29px}
</style>
</head>
<body>
<header class="site-header">
  <div class="brand">DARREN KOVAL</div>
  <nav class="nav"><span class="active">HOME</span><span>ABOUT ME</span><span>SERVICES</span><span>CLIENTS</span><span>CONTACT ME</span></nav>
</header>

<section class="hero">
  <svg class="hero-ring" width="1200" height="446" viewBox="0 0 1200 446">
    <circle cx="826" cy="238" r="208" fill="none" stroke="var(--green)" stroke-width="44"/>
    <path d="M826 30 A208 208 0 0 1 960 430" fill="none" stroke="var(--green-dark)" stroke-width="44"/>
  </svg>
  <div class="hero-portrait" role="img" aria-label="Portrait of Dr Darren Koval in a blue shirt"></div>
  <h1 class="hero-title">DR DARREN KOVAL</h1>
  <div class="phone-box">
    <svg width="30" height="30" viewBox="0 0 24 24" fill="none" stroke="#fff" stroke-width="2" stroke-linecap="round" stroke-linejoin="round"><path d="M22 16.9v3a2 2 0 0 1-2.2 2 19.8 19.8 0 0 1-8.6-3.1 19.5 19.5 0 0 1-6-6A19.8 19.8 0 0 1 2.1 4.2 2 2 0 0 1 4.1 2h3a2 2 0 0 1 2 1.7c.1 1 .4 1.9.7 2.8a2 2 0 0 1-.5 2.1L8 9.9a16 16 0 0 0 6 6l1.3-1.3a2 2 0 0 1 2.1-.4c.9.3 1.8.6 2.8.7a2 2 0 0 1 1.8 2z"/><path d="M15 2a7 7 0 0 1 7 7M15 6a3 3 0 0 1 3 3"/></svg>
    <span>+1 555 014 2290</span>
  </div>
  <div class="book-btn">BOOK ONLINE</div>
</section>

<section class="features">
  <div class="feature" style="width:347px">
    <svg width="32" height="32" viewBox="0 0 24 24" fill="#fff"><rect x="3" y="13" width="6" height="8" rx="1" transform="rotate(-45 6 17)"/><rect x="15" y="3" width="6" height="8" rx="1" transform="rotate(-45 18 7)"/><rect x="8" y="10.5" width="8" height="3" transform="rotate(-45 12 12)"/></svg>LARGE GYM</div>
  <div class="feature" style="width:268px">
    <svg width="30" height="30" viewBox="0 0 24 24" fill="#fff"><path d="M8 3h8v3h4a2 2 0 0 1 2 2v12a2 2 0 0 1-2 2H4a2 2 0 0 1-2-2V8a2 2 0 0 1 2-2h4zM10 5v1h4V5z"/><circle cx="12" cy="14" r="5" fill="var(--green)"/><path d="M11 11h2v2h2v2h-2v2h-2v-2H9v-2h2z"/></svg>MEDICAL</div>
  <div class="feature" style="width:263px">
    <svg width="30" height="30" viewBox="0 0 24 24" fill="none" stroke="#fff" stroke-width="2"><path d="M4 14a8 8 0 0 1 16 0v7H4z"/><circle cx="12" cy="13" r="3"/></svg>IMAGING</div>
  <div class="feature" style="width:322px">
    <svg width="26" height="30" viewBox="0 0 20 24" fill="#fff"><rect x="4" y="0" width="12" height="4" rx="1"/><path d="M2 6h16v18H2z"/><path d="M9 11h2v3h3v2h-3v3H9v-3H6v-2h3z" fill="var(--green)"/></svg>PHARMACY</div>
</section>

<section class="experience">
  <h2 class="section-title exp-title">MY EXPERIENCE</h2>
  <div class="photo photo-gym" role="img" aria-label="Clinic gym with treadmills and exercise equipment"></div>
  <div class="photo photo-clinic" role="img" aria-label="Dr Koval standing beside a gait analysis machine"></div>
  <div class="exp-text">
    <p>Darren graduated from Harbourline University in 1992 with the university prize for clinical excellence. After roles in surgical, ICU, orthopedics, amputee rehabilitation, and outpatient clinics, Darren accepted a role with the National Defence Service where he later became department senior and area health manager for injury surveillance and prevention. Roles with local, national, International rugby and cricket, and clinical roles with Olympic squads led to completion of a Master of Sports Physiotherapy in 1999, with 2 academic excellence awards. Darren's leadership and governance skills have developed through service on multiple corporate, academic, professional and community boards. The Sports Injury Clinic he had established in his home became a larger commercial practice. With Darren as founder, director and CEO, the company won more than 500+ government tenders over 8 years and grew to employ 120 allied health and medical staff nationwide. In 2004 Darren helped establish the first Physiotherapy course in Wexmoor, now graduating approximately 100 top ranked clinicians per year. Accepting a full-time tenured position at Wexmoor University in 2008, Darren completed a Graduate Certificate in Higher Education. Darren's expertise in teaching has been recognised with 4 teaching awards nominated by his peers and students. Eventually having time to complete a PhD in 2017 (Medial Tibial Stress Syndrome), Darren is since supervising multiple PhD projects predominantly in sports and military projects. Research interests are in musculoskeletal injury prevention and management, particularly medial tibial stress syndrome, motor control in anterior cruciate ligament injury, clinical prediction, and spinal pain in military aircrew. These interests and connections internationally have resulted in significant success in research funding (over $3M as bid leader), 2 external research prizes, and commercialisation opportunities. Darren is an experienced international speaker and author of around 40 peer-reviewed papers.</p>
    <p>Darren continues to add to his 30+ years as a clinician working at the University Clinic alongside his academic roles as educator, researcher and mentor.</p>
  </div>
</section>

<section class="services">
  <h2 class="section-title">OUR SERVICES</h2>
  <div class="services-rule"></div>
  <div class="service" style="left:132px"><div class="pic pic-msk" role="img" aria-label="X-ray style illustration of a painful shoulder"></div><h3>MUSCULOSKELETAL CONDITIONS</h3></div>
  <div class="service" style="left:452px"><div class="pic pic-limb" role="img" aria-label="Hands holding an inflamed knee"></div><h3>LOWER LIMB DIAGNOSIS</h3></div>
  <div class="service" style="left:771px"><div class="pic pic-rehab" role="img" aria-label="Physiotherapist stretching a patient's leg"></div><h3>REHABILITATION</h3></div>
</section>

<section class="map" role="img" aria-label="Street map showing the clinic location"></section>

<footer class="site-footer">
  <div class="footer-top">
    <div class="brand">DARREN KOVAL</div>
    <nav class="nav"><span>HOME</span><span>ABOUT ME</span><span>SERVICES</span><span>CLIENTS</span><span>CONTACT ME</span></nav>
  </div>
  <div class="footer-rule"></div>
  <p class="copyright">Copyright © 2022 All Rights Reserved</p>
</footer>
</body>
</html>
```